Design and Renovation Company Luxury Business Card

I want to create a luxury business card for a Design and Renovation Firm . We will use our current logo. The company name is 528BUILDA. We do not want anything standard. We need a very unique concept.
Please see uploaded inspiration. I really like the textured paper option. I would like the card to be thick with debossing, and/or embossing options. The logo has orange in it but I would like to see the card with and without the orange. I think the orange may make the company feel less high-end. The goal is to elevate the logo not match its vibe per se of the logo. We want something very unique, not standard at all!
I would like a space for :
Logo,
Name,
Position,
Email,
Office number,
Website Address,
Business Address,
Thank you!
Have fun!
Target Market(s)
Home owners Age 35 +
Industry/Entity Type
Design and Renovation
Contact Information for Business Card
Logo, Name, Position, Email, Office number, Website Address, Business Address,.
Colors
Designer to choose colors to be used in the design.
Requirements
Must have
- A luxury designer feel. Must be black or dark grey but open to other luxury ideas.
Nice to have
- Gold, silver, black embossing or debossing. Textured paper design.
Should not have
- A cheap look and feel.

```html
<!DOCTYPE html>
<html lang="en">
<head>
<meta charset="UTF-8">
<title>528BUILDA Business Card</title>
<link href="https://fonts.googleapis.com/css2?family=Montserrat:wght@400;500;700&display=swap" rel="stylesheet">
<style>
  :root{
    --bg:#2b2d31;
    --card-white:#ffffff;
    --ink:#1a1a1a;
    --black:#0d0d0d;
    --orange:#f7931e;
  }
  *{margin:0;padding:0;box-sizing:border-box}
  html,body{width:1200px;height:900px;overflow:hidden}
  body{background:var(--bg);position:relative;font-family:"Montserrat",sans-serif}
  .card{position:absolute;left:300px;width:600px;height:343px;border-radius:6px;overflow:hidden;box-shadow:0 10px 30px rgba(0,0,0,.45)}
  .card-front{top:70px;background:var(--card-white)}
  .card-back{top:487px;background:var(--black)}
  .edge-band{position:absolute;width:22px;background:var(--black)}
  .edge-band.top-left{left:0;top:0;height:135px}
  .edge-band.bottom-right{right:0;bottom:0;height:160px}
  .company-name{position:absolute;font-family:"Montserrat",sans-serif;font-weight:500;letter-spacing:3px;line-height:1;white-space:nowrap}
  .card-front .company-name{left:62px;top:140px;font-size:28px;color:var(--ink)}
  .divider{position:absolute;left:318px;top:92px;width:2px;height:170px;background:var(--orange)}
  .contact{position:absolute;left:336px;top:94px;color:var(--ink)}
  .person-name{font-size:22px;font-weight:700;color:var(--orange);line-height:1.1}
  .person-role{font-size:12px;margin-bottom:10px}
  .address{font-size:12px;line-height:1.35;margin-bottom:8px}
  .contact-line{display:flex;align-items:center;gap:7px;font-size:12px;line-height:1.55}
  .contact-line svg{width:10px;height:10px;flex:none}
  .pattern{position:absolute;inset:0;background:linear-gradient(120deg,#050505 0%,#151515 45%,#3a3a3a 100%)}
  .card-back .company-name{left:50%;top:50%;transform:translate(-50%,-50%);font-size:38px;color:#ffffff}
</style>
</head>
<body>
  <section class="card card-front">
    <div class="edge-band top-left"></div>
    <div class="edge-band bottom-right"></div>
    <p class="company-name">528BUILDA</p>
    <div class="divider"></div>
    <div class="contact">
      <p class="person-name">Daniel Harrow</p>
      <p class="person-role">Managing Director</p>
      <p class="address">415 Linden Park Ave #112<br>Fairmont, OH 43219</p>
      <p class="contact-line"><svg viewBox="0 0 10 10"><path d="M2 1l2 2-1 1.2a6 6 0 0 0 2.8 2.8L7 6l2 2-1.2 1.2C4.5 9 1 5.5.8 2.2z" fill="var(--orange)"/></svg>614-555-0183</p>
      <p class="contact-line"><svg viewBox="0 0 10 10"><rect x="0.5" y="2" width="9" height="6.5" rx="1" fill="var(--orange)"/><path d="M1 2.6L5 5.6 9 2.6" stroke="#fff" stroke-width="1" fill="none"/></svg>hello@528builda.com</p>
      <p class="contact-line"><svg viewBox="0 0 10 10"><circle cx="5" cy="5" r="4.3" fill="none" stroke="var(--orange)" stroke-width="1.2"/><path d="M.8 5h8.4M5 .8c-2 2.5-2 5.9 0 8.4M5 .8c2 2.5 2 5.9 0 8.4" stroke="var(--orange)" stroke-width=".9" fill="none"/></svg>www.528builda.com</p>
    </div>
  </section>

  <section class="card card-back">
    <div class="pattern" role="img" aria-label="Decorative grid of black and grey tiles fading diagonally across the card"></div>
    <p class="company-name">528BUILDA</p>
  </section>
</body>
</html>
```